Personal Injury Lawyer Billboard

I would like a design created featuring the image of the lawyer centered in the middle of the design.
To the left of the lawyer's image it should read "INJURED?"
To the right of the lawyer's image, it should read "CALL DEAN!"
Under Call Dean, include the phone number 318-555-0187.
At the bottom of the design include the lawyers information "Dean Marlowe Accident & Injury Lawyers"
PLEASE REMOVED THE BACKGROUND IMAGERY OF THE PHOTO SUBMITTED. Also, the colors for this design should match the colors shown in the logo (navy, white and relective soft gold). Please use those color combinations in ways that best stand out.

```html
<!DOCTYPE html>
<html lang="en">
<head>
<meta charset="utf-8">
<title>Dean Marlowe Accident &amp; Injury Lawyers Billboard</title>
<link href="https://fonts.googleapis.com/css2?family=Cinzel:wght@400;500&family=Libre+Caslon+Text:wght@400&display=swap" rel="stylesheet">
<style>
  :root {
    --navy: #0b1c47;
    --navy-deep: #081538;
    --gold: #c9a23f;
    --white: #ffffff;
    --ink: #111111;
    --stage: #e9eaee;
  }
  * { margin: 0; padding: 0; box-sizing: border-box; }
  html, body {
    width: 1200px;
    height: 879px;
    overflow: hidden;
    background: var(--stage);
  }
  .billboard {
    position: absolute;
    left: 0;
    top: 206px;
    width: 1200px;
    height: 466px;
    background: var(--navy);
    overflow: hidden;
  }
  .headline {
    position: absolute;
    left: 40px;
    top: 160px;
    font-family: "Cinzel", serif;
    font-weight: 400;
    font-size: 86px;
    letter-spacing: 3px;
    line-height: 1;
    color: var(--gold);
  }
  .firm {
    position: absolute;
    left: 40px;
    top: 322px;
    font-family: "Libre Caslon Text", serif;
    font-weight: 400;
    color: var(--white);
    line-height: 1;
  }
  .firm-name {
    display: block;
    font-size: 46px;
    letter-spacing: -1px;
    text-transform: uppercase;
  }
  .firm-tagline {
    display: block;
    margin-top: 20px;
    font-size: 21px;
    letter-spacing: 0;
    text-transform: uppercase;
  }
  .portrait {
    position: absolute;
    left: 452px;
    top: 17px;
    width: 338px;
    height: 449px;
    border-radius: 150px 150px 0 0;
    background: linear-gradient(180deg, #2a2f4a 0%, #1a2550 45%, #101c44 100%);
  }
  .cta {
    position: absolute;
    left: 778px;
    top: 150px;
    width: 422px;
    height: 185px;
    background: var(--gold);
    border-radius: 92px 0 0 92px;
    font-family: "Cinzel", serif;
    color: var(--ink);
  }
  .cta-label {
    position: absolute;
    left: 56px;
    top: 38px;
    font-size: 56px;
    font-weight: 400;
    line-height: 1;
    letter-spacing: 1px;
  }
  .cta-phone {
    position: absolute;
    left: 56px;
    top: 112px;
    display: flex;
    align-items: center;
    gap: 14px;
    font-size: 42px;
    line-height: 1;
  }
  .cta-phone svg { width: 46px; height: 46px; flex: none; }
</style>
</head>
<body>
  <section class="billboard">
    <h1 class="headline">INJURED</h1>

    <div class="firm">
      <span class="firm-name">Dean Marlowe</span>
      <span class="firm-tagline">Accident &amp; Injury Lawyers</span>
    </div>

    <div class="portrait" role="img" aria-label="Portrait of the smiling lawyer in a navy suit and green tie, raising a fist"></div>

    <div class="cta">
      <p class="cta-label">CALL DEAN</p>
      <p class="cta-phone">
        <svg viewBox="0 0 46 46" aria-hidden="true">
          <circle cx="23" cy="23" r="20" fill="none" stroke="#111" stroke-width="3.5"/>
          <path d="M15 13c1-1 2.5-1 3.3 0l2.4 3.2c.7 1 .6 2.2-.2 3l-1.4 1.4c1.2 2.6 3.2 4.6 5.8 5.8l1.4-1.4c.8-.8 2-.9 3-.2l3.2 2.4c1 .8 1 2.3 0 3.3l-1.5 1.5c-1.5 1.5-3.8 1.9-5.7 1-5.5-2.4-9.6-6.5-12-12-.9-1.9-.5-4.2 1-5.7z" fill="#111"/>
          <path d="M25 13a8 8 0 0 1 8 8M25 17.5a3.5 3.5 0 0 1 3.5 3.5" fill="none" stroke="#111" stroke-width="2.2" stroke-linecap="round"/>
        </svg>
        318-555-0187
      </p>
    </div>
  </section>
</body>
</html>
```